Signage Design Project

Busisness is a bakery and deli long time owned by the Tavel family. Want to develop a new outside sign that communicates it is a deli and a bakery but keeps the tavel name in the design.

The sign when produced will be about 10' by 3' . It is not lighted at present but could be if it were advantageous.

The name of the store is:

Tavel's Harbor Lane Bakery and Deli. The concept is to have a new,modern sign that reinforces that it is a deli and a bakery, as most people only know about the bakery side of the business
Updates

The name Tavel is just a reinforcer so the people kno it is still in the family.  The emphasis should be on the HARBOR LANE BAKERY and DELI

Target Market(s)

Small business breakfast and lunch customers

Industry/Entity Type

Bakery

Requirements
Must have
• Great impact from the road. Communicate that it is a deli and a bakery. Keep the Tavel name but need not be a major design element

```html
<!DOCTYPE html>
<html lang="en">
<head>
<meta charset="utf-8">
<title>Tavel's Harbor Lane Bakery and Deli – Sign</title>
<link rel="stylesheet" href="https://fonts.googleapis.com/css2?family=Righteous&display=swap">
<style>
  :root {
    --sign-core: #8f1a4a;
    --sign-edge: #55031f;
    --letter: #ffffff;
    --letter-shadow: #000000;
  }
  html, body {
    margin: 0;
    padding: 0;
    width: 1200px;
    height: 360px;
    overflow: hidden;
  }
  .sign {
    position: relative;
    width: 1200px;
    height: 360px;
    background: radial-gradient(ellipse 70% 90% at 50% 45%, var(--sign-core) 0%, #7d1340 55%, var(--sign-edge) 100%);
    font-family: "Righteous", "Arial Black", sans-serif;
    color: var(--letter);
    text-align: center;
    white-space: nowrap;
  }
  .sign-name {
    position: absolute;
    top: 56px;
    left: 0;
    right: 0;
    margin: 0;
    line-height: 1;
    text-shadow: -4px 4px 0 var(--letter-shadow);
  }
  .family-name {
    font-size: 60px;
    margin-right: 14px;
    vertical-align: 4px;
  }
  .location-name {
    font-size: 80px;
  }
  .sign-services {
    position: absolute;
    top: 160px;
    left: 0;
    right: 0;
    margin: 0;
    font-size: 160px;
    line-height: 1;
    letter-spacing: 4px;
    text-shadow: -6px 6px 0 var(--letter-shadow);
  }
</style>
</head>
<body>
  <main class="sign">
    <h1 class="sign-name">
      <span class="family-name">Tavel's</span><span class="location-name">Harbor Lane</span>
    </h1>
    <p class="sign-services">Bakery &amp; Deli</p>
  </main>
</body>
</html>
```